American cannabis tech company business card design

Pavrel.com is seeking a modern, professional, and brand-aligned business card that represents our company and its core values: Mission, Story, Values, and Impact. As an innovative cannabis company, we want a business card that is not only visually appealing but also serves as a representation of who we are and what we stand for.

Project Scope: Design a double-sided business card that integrates our brand identity and core values. Incorporate our key brand elements, ensuring a sleek and contemporary aesthetic. Visually reflect our core values (Mission, Story, Values, Impact) in a way that is engaging yet professional.

Target Market(s)

Vendors, third parties,

Contact Information for Business Card

Contact details (name, title, email, phone, website, etc.)

Font styles to use
Other font styles liked:
• Caslon, Centra

Colors

Designer to choose colors to be used in the design.

Requirements
Must have
• Pavrel.com logo and branding A creative yet clean way to integrate our core values (Mission, Story, Values, Impact) Modern typography and a well-structured layout
Nice to have
• forest green, grey, white, black
Should not have
• references to marijuana, leafs, plants, or related product

```html
<!DOCTYPE html>
<html lang="en">
<head>
<meta charset="utf-8">
<title>Pavrel.com Business Card</title>
<link href="https://fonts.googleapis.com/css2?family=Poppins:wght@400;600;800&display=swap" rel="stylesheet">
<style>
  :root {
    --backdrop: #e8e8e8;
    --card-white: #f4f4f4;
    --forest: #17321a;
    --ink-light: #ffffff;
  }
  * { margin: 0; padding: 0; box-sizing: border-box; }
  html, body { width: 1200px; height: 1200px; overflow: hidden; }
  body {
    background: var(--backdrop);
    font-family: "Poppins", sans-serif;
    position: relative;
  }
  .card {
    position: absolute;
    top: 311px;
    width: 363px;
    height: 593px;
    border-radius: 16px;
  }
  .card--front { left: 234px; background: var(--card-white); }
  .card--back { left: 627px; background: var(--forest); color: var(--ink-light); }

  .wordmark {
    position: absolute;
    font-family: "Poppins", sans-serif;
    font-weight: 800;
    font-size: 56px;
    line-height: 1;
    letter-spacing: 1px;
  }
  .card--front .wordmark {
    left: 0; right: 0; top: 268px;
    text-align: center;
    color: var(--forest);
  }
  .card--back .wordmark {
    left: 52px; top: 140px;
    color: var(--ink-light);
  }

  .holder { position: absolute; left: 52px; top: 280px; }
  .holder__name { font-weight: 600; font-size: 21px; letter-spacing: 0.5px; line-height: 1.2; }
  .holder__title { font-weight: 400; font-size: 16.5px; line-height: 1.3; }

  .contacts { position: absolute; left: 53px; top: 343px; list-style: none; }
  .contacts li {
    display: flex; align-items: center; gap: 5px;
    font-size: 16.5px; line-height: 22px;
  }
  .contacts svg { width: 16px; height: 16px; flex: none; }

  .address {
    position: absolute; left: 54px; top: 425px;
    font-size: 16.5px; line-height: 22px; font-style: normal;
  }
</style>
</head>
<body>
  <section class="card card--front" aria-label="Business card front">
    <div class="wordmark">PAVREL</div>
  </section>

  <section class="card card--back" aria-label="Business card back">
    <div class="wordmark">PAVREL</div>
    <div class="holder">
      <p class="holder__name">DANIEL BROOKS</p>
      <p class="holder__title">Managing Director</p>
    </div>
    <ul class="contacts">
      <li>
        <svg viewBox="0 0 16 16" fill="none" stroke="#fff" stroke-width="1.5" stroke-linejoin="round">
          <path d="M3 2.5l2.5-.5 1.5 3-1.5 1.2a8 8 0 0 0 4.3 4.3L11 9l3 1.5-.5 2.5c-6 .5-11-4.5-10.5-10.5z"/>
        </svg>
        044-318 620 754
      </li>
      <li>
        <svg viewBox="0 0 16 16">
          <rect x="1.5" y="3.5" width="13" height="9.5" rx="1" fill="#fff"/>
          <path d="M2 4.5l6 4.5 6-4.5" fill="none" stroke="#17321a" stroke-width="1.3"/>
        </svg>
        info@pavrel.com
      </li>
      <li>
        <svg viewBox="0 0 16 16" fill="none" stroke="#fff" stroke-width="1.3">
          <circle cx="8" cy="8" r="6.3"/>
          <ellipse cx="8" cy="8" rx="2.8" ry="6.3"/>
          <path d="M1.7 8h12.6M2.6 5h10.8M2.6 11h10.8"/>
        </svg>
        www.pavrel.com
      </li>
    </ul>
    <address class="address">
      218, Harlow Avenue Suite 4<br>
      Denver 80202, USA
    </address>
  </section>
</body>
</html>
```